Brivolt Technologies business card design

We need a business card designed with our new logo. it would be great if the card could communicate it is a technology based company.

Target Market(s)

system integrators

Industry/Entity Type

technology, IOT

Contact Information for Business Card

Name, designation, Address, telephone number, email address

Requirements
Must have
• logo and company name
Nice to have
• something to do with technology

```html
<!DOCTYPE html>
<html lang="en">
<head>
<meta charset="utf-8">
<title>Brivolt Technologies – Business Card</title>
<link rel="stylesheet" href="https://fonts.googleapis.com/css2?family=Poppins:wght@400;500;700&display=swap">
<style>
  :root {
    --stage: #2f2f2f;
    --card-white: #ffffff;
    --brand-orange: #f39117;
    --brand-orange-deep: #e47f0f;
    --ink-dark: #333333;
    --ink-body: #3d3d3d;
    --rule-grey: #c9c9c9;
  }
  * { box-sizing: border-box; margin: 0; padding: 0; }
  html, body {
    width: 1200px; height: 866px; overflow: hidden;
    background: var(--stage);
    font-family: "Poppins", sans-serif;
  }
  .stage {
    width: 1200px; height: 866px;
    display: flex; align-items: center; justify-content: center; gap: 40px;
  }
  .card {
    position: relative;
    width: 540px; height: 308px;
    box-shadow: 0 10px 24px rgba(0,0,0,.45);
    overflow: hidden;
  }

  /* Front */
  .card-front { background: var(--card-white); }
  .card-front .edge-band {
    position: absolute; left: 0; right: 0; bottom: 0; height: 8px;
    display: flex;
  }
  .edge-band .band-dark { flex: 0 0 44%; background: var(--ink-dark); }
  .edge-band .band-orange { flex: 1; background: var(--brand-orange); }

  .front-brand {
    position: absolute; left: 34px; top: 0; bottom: 8px; width: 190px;
    display: flex; align-items: center; gap: 10px;
  }
  .brand-square {
    flex: 0 0 auto; width: 18px; height: 18px; background: var(--brand-orange);
  }
  .brand-name {
    font-weight: 700; color: var(--ink-dark);
    text-transform: uppercase; line-height: 1.1;
    font-size: 25px; letter-spacing: .5px;
  }
  .brand-name .line-2 { display: block; font-size: 15.5px; letter-spacing: 2.6px; }

  .divider {
    position: absolute; left: 240px; top: 70px; height: 160px;
    width: 1px; background: var(--rule-grey);
  }

  .contact {
    position: absolute; left: 262px; top: 74px; right: 20px;
    color: var(--ink-body); font-size: 13.5px; line-height: 1.45;
  }
  .contact .person-name {
    color: var(--brand-orange); font-weight: 700; font-size: 17px;
    text-transform: uppercase; letter-spacing: .6px; line-height: 1.2;
  }
  .contact .person-role { font-size: 14px; margin-bottom: 6px; }
  .contact .row { display: flex; align-items: center; gap: 7px; }
  .contact .row svg { width: 12px; height: 12px; flex: 0 0 auto; }
  .contact .address { margin-top: 4px; }

  /* Back */
  .card-back {
    background: var(--brand-orange);
    display: flex; align-items: center; justify-content: center;
  }
  .back-pattern {
    position: absolute; inset: 0;
    background: linear-gradient(135deg, var(--brand-orange) 0%, var(--brand-orange-deep) 55%, var(--brand-orange) 100%);
  }
  .back-brand {
    position: relative; display: flex; align-items: center; gap: 14px;
  }
  .back-brand .brand-square { width: 26px; height: 26px; background: var(--ink-dark); }
  .back-brand .brand-name { font-size: 40px; }
  .back-brand .brand-name .line-2 { font-size: 22.5px; letter-spacing: 4.6px; }
</style>
</head>
<body>
<main class="stage">

  <section class="card card-front" aria-label="Business card front">
    <div class="front-brand">
      <span class="brand-square"></span>
      <p class="brand-name">Brivolt<span class="line-2">Technologies</span></p>
    </div>
    <div class="divider"></div>
    <div class="contact">
      <p class="person-name">Dorian Kestrel</p>
      <p class="person-role">Managing Director</p>
      <p class="row">
        <svg viewBox="0 0 12 12" aria-hidden="true"><path fill="#f39117" d="M1 4c0-2 2-3 5-3s5 1 5 3l-2 1-1-2H4L3 5 1 4zm2 2h6l1 5H2l1-5zm3 1.2a1.3 1.3 0 1 0 0 2.6 1.3 1.3 0 0 0 0-2.6z"/></svg>
        1298473650
      </p>
      <p class="row">
        <svg viewBox="0 0 12 12" aria-hidden="true"><rect x="0.5" y="2" width="11" height="8" fill="#f39117"/><path d="M0.5 2 6 6.5 11.5 2" fill="none" stroke="#fff" stroke-width="1"/></svg>
        info@website.com
      </p>
      <p class="address">25634 Address line here<br>Country code, Country Name</p>
    </div>
    <div class="edge-band"><span class="band-dark"></span><span class="band-orange"></span></div>
  </section>

  <section class="card card-back" aria-label="Business card back">
    <div class="back-pattern" role="img" aria-label="Overlapping translucent orange squares pattern"></div>
    <div class="back-brand">
      <span class="brand-square"></span>
      <p class="brand-name">Brivolt<span class="line-2">Technologies</span></p>
    </div>
  </section>

</main>
</body>
</html>
```